MEDICAL CLINIC LETTERHEAD

Design is a letterhead for a non-profit medical center. The name of the clinic is VITARIDGE Community Health Center. Although the full name must be included, the community health center part is more of a description and should be less visible - i attached an example of what I mean by that (ATTACHED IMAGE IS AN EXAMPLE OF FONT SIZES NOT A DESIGN IDEA). Please design something modern, cool looking and unique because I can always download free templates.
Phone, email, website and etc will be added later.

Industry/Entity Type

MEDICAL

```html
<!DOCTYPE html>
<html lang="en">
<head>
<meta charset="utf-8">
<title>VITARIDGE Community Health Center – Letterhead</title>
<link rel="stylesheet" href="https://fonts.googleapis.com/css2?family=Lato:wght@400;700&family=Mulish:wght@400;500&display=swap">
<style>
  :root {
    --navy: #1b2849;
    --gold: #b39058;
    --ink: #3a3a3a;
    --contact-ink: #161616;
    --paper: #ffffff;
    --paper-edge: #f1f0f0;
    --backdrop: #e3e3e3;
  }
  * { box-sizing: border-box; margin: 0; padding: 0; }
  html, body {
    width: 1153px; height: 1200px; overflow: hidden;
    background: var(--backdrop);
  }
  .letterhead {
    position: absolute; left: 162px; top: 20px;
    width: 829px; height: 1160px;
    background: radial-gradient(ellipse 60% 45% at 50% 38%, var(--paper) 40%, var(--paper-edge) 100%);
    font-family: "Lato", sans-serif;
    color: var(--ink);
    overflow: hidden;
  }
  .brand {
    position: absolute; left: 60px; top: 82px;
    display: flex; align-items: center; gap: 10px;
  }
  .brand-mark {
    width: 14px; height: 14px; background: var(--gold);
  }
  .brand-name {
    font-family: "Lato", sans-serif; font-weight: 700;
    font-size: 40px; letter-spacing: 1px; color: var(--navy);
    line-height: 1;
  }
  .contact {
    position: absolute; left: 567px; top: 48px;
    border-left: 1.5px solid var(--gold);
    padding-left: 12px; height: 92px;
    font-family: "Mulish", sans-serif; color: var(--contact-ink);
  }
  .contact-name { font-size: 14px; line-height: 18px; font-weight: 500; }
  .contact-list { list-style: none; margin-top: 7px; }
  .contact-list li {
    display: flex; align-items: center; gap: 10px;
    font-size: 14px; line-height: 19.5px;
  }
  .contact-list svg { width: 14px; height: 12px; fill: var(--gold); flex: none; }
  .letter {
    position: absolute; left: 64px; top: 256px; width: 701px;
    font-size: 15px; line-height: 18.6px;
  }
  .letter-date { font-size: 16px; }
  .recipient { margin-top: 20px; }
  .recipient-company { margin-top: 19px; }
  .salutation {
    margin-top: 18px; font-size: 19px; font-weight: 700; color: var(--ink);
  }
  .body-copy p {
    margin-top: 17px; text-align: justify; font-size: 14.5px; line-height: 17.8px;
  }
  .body-copy p:first-child { margin-top: 22px; }
  .closing { margin-top: 40px; font-size: 15px; }
  .signature {
    margin-top: 22px; width: 205px; height: 42px;
    background: linear-gradient(90deg, rgba(58,58,58,0.16), rgba(58,58,58,0.05));
    border-radius: 4px;
  }
  .footer-wave {
    position: absolute; left: 0; bottom: 0; width: 829px; height: 128px; display: block;
  }
</style>
</head>
<body>
  <main class="letterhead">
    <header>
      <div class="brand">
        <span class="brand-mark"></span>
        <span class="brand-name">VITARIDGE</span>
      </div>
      <address class="contact" style="font-style:normal">
        <div class="contact-name">VITARIDGE Community<br>Health Center</div>
        <ul class="contact-list">
          <li>
            <svg viewBox="0 0 14 12" aria-hidden="true"><path d="M1 4c0-2 3-3 6-3s6 1 6 3v1h-3V4H4v1H1zM3 6h8l2 5H1z"/></svg>
            555-214-3670
          </li>
          <li>
            <svg viewBox="0 0 14 12" aria-hidden="true"><path d="M0 2h14v1L7 7 0 3zM0 4.5l7 4 7-4V11H0z"/></svg>
            hello@vitaridge-care.org
          </li>
          <li>
            <svg viewBox="0 0 14 12" aria-hidden="true"><circle cx="7" cy="6" r="5.5"/></svg>
            www.vitaridge-care.org
          </li>
        </ul>
      </address>
    </header>

    <article class="letter">
      <p class="letter-date">Feb-03-2022</p>
      <p class="recipient">Mr, Daniel Reeve<br>President</p>
      <p class="recipient-company">Northgate Holdings<br>48 Alder Lane, Suite# 12<br>Fairview, State, 104857</p>
      <h1 class="salutation">Dear Mr, Daniel</h1>
      <div class="body-copy">
        <p>Lorem ipsum dolor sit amet, consectetur adipisicing elit, sed do eiusmod tempor incididunt ut labore et dolore magna aliqua. Ut enim ad minim veniam, quis nostrud exercitation ullamco laboris nisi ut aliquip ex ea commodo consequat. Duis aute irure dolor in reprehenderit in voluptate velit esse cillum dolore eu fugiat nulla pariatur.</p>
        <p>Lorem ipsum dolor sit amet, consectetur adipisicing elit, sed do eiusmod tempor incididunt ut labore et dolore magna aliqua. Ut enim ad minim veniam, quis nostrud exercitation ullamco laboris nisi ut aliquip ex ea commodo consequat. Duis aute irure dolor in reprehenderit in voluptate velit esse cillum dolore eu fugiat nulla pariatur.</p>
        <p>Lorem ipsum dolor sit amet, consectetur adipisicing elit, sed do eiusmod tempor incididunt ut labore et dolore magna aliqua. Ut enim ad minim veniam, quis nostrud exercitation ullamco laboris nisi ut aliquip ex ea commodo consequat.</p>
        <p>Excepteur sint occaecat cupidatat non proident, sunt in culpa qui officia deserunt mollit anim id est laborum. re et dolore magnam aliquam quaerat voluptatem.</p>
      </div>
      <p class="closing">Regards</p>
      <div class="signature" role="img" aria-label="Handwritten signature of Owen Hartley"></div>
    </article>

    <svg class="footer-wave" viewBox="0 0 1068 164" preserveAspectRatio="none" aria-hidden="true">
      <path d="M0 0 Q534 240 1068 0 L1068 164 L0 164 Z" fill="var(--navy)"/>
      <path d="M48 12 Q534 196 1000 18 Q534 180 48 12 Z" fill="var(--gold)"/>
    </svg>
  </main>
</body>
</html>
```